Halvik - consultancy website

I need a new design for my webpage/presence [to be functioning with Wordpress - I have a programmer to set it up but not the design idea].
My company is Halvik - a consultancy firm focused on growth management for Swedish SME's primarily;. We call it Leadership toolkit for firms on the rise, kind of a doctor helping small become big. Contentwise, its a simple frontpage + 3-4 subpages with content re company/myself/focus etc. The new site should communicate a fresh, trustworthy take yet simple and functional on all devices [i.e. think UI compatible for mobile/tablet]. Current building parts/form elements are
a) existing logo and text elements
b) existing pictures
c) the yellowish color
colours and new ideas on pictures/positioning are welcome. I prefer a 'full width page' solution with centralised text elements but that's all up to you to suggest. Current site is a quickfix made by myself - now I'm moving it to a new platform so want to take the opportunity to make it
Nothing superspecial as it is a 2-man show; on the other hand I still want to have a modern & fresh reflection of my brand in digital environments. Help me out!
www.halvik-demo.se
Best
Lina Bergqvist

```html
<!DOCTYPE html>
<html lang="en">
<head>
<meta charset="utf-8">
<title>Halvik – Growth management consultancy</title>
<link href="https://fonts.googleapis.com/css2?family=Roboto+Slab:wght@300;400;500;700&display=swap" rel="stylesheet">
<style>
:root{
  --orange:#f0a33a;
  --orange-dark:#e8962a;
  --ink:#222222;
  --text:#555555;
  --muted:#8a8a8a;
  --line:#e6e6e6;
  --nav-bg:#ececec;
  --night:#1f1a1c;
  --footer:#1d1d1d;
  --footer-bottom:#121212;
  --white:#ffffff;
  --blue:#3b5998;
  --sky:#3aa6e0;
  --red:#d9483b;
  --accent-red:#d9363e;
}
*{margin:0;padding:0;box-sizing:border-box}
html,body{width:1200px;height:2236px;overflow:hidden}
body{font-family:"Roboto Slab",Georgia,serif;color:var(--text);background:var(--white);position:relative}
.wrap{position:absolute;left:98px;width:1004px}

/* header */
.site-header{position:absolute;top:0;left:0;width:1200px;height:135px}
.brand{position:absolute;left:100px;top:26px}
.brand-name{font-size:50px;font-weight:400;color:var(--ink);line-height:1;letter-spacing:-0.5px}
.brand-tagline{font-size:13px;color:var(--ink);margin-top:6px}
.main-nav{position:absolute;left:580px;top:50px;display:flex;gap:5px}
.main-nav a{display:block;width:106px;height:38px;line-height:38px;text-align:center;background:var(--nav-bg);color:var(--ink);font-size:13px;text-decoration:none}
.main-nav a.active{color:var(--orange);border-bottom:2px solid var(--orange)}

/* hero */
.hero{position:absolute;top:135px;left:0;width:1200px;height:449px;background:var(--orange);box-shadow:0 8px 12px -6px rgba(0,0,0,.18)}
.hero-photo{position:absolute;left:0;top:0;width:444px;height:449px;background:linear-gradient(90deg,#e4e4e4,#f4f4f4 60%,#ececec)}
.hero-text{position:absolute;right:112px;top:158px;text-align:right;color:var(--white);font-size:26px;font-weight:300;line-height:32px}
.btn-dark{position:absolute;right:114px;top:240px;width:105px;height:32px;line-height:32px;background:#111;color:var(--white);font-size:13px;text-align:center}
.hero-dots{position:absolute;right:18px;bottom:14px;display:flex;gap:6px}
.hero-dots span{width:9px;height:9px;border-radius:50%;border:1px solid #222}
.hero-dots span.on{background:#222}

/* about */
.about{top:628px;text-align:center}
.section-title{font-size:27px;font-weight:400;color:var(--ink)}
.about p{margin-top:22px;font-size:11.5px;line-height:22.5px;color:var(--text)}
.btn-orange{display:inline-block;margin-top:22px;width:120px;height:33px;line-height:33px;background:var(--orange);color:var(--white);font-size:14px}

/* services */
.services{top:910px;height:247px;display:flex;border:1px solid var(--line)}
.service{width:251px;text-align:center;border-right:1px solid var(--line);position:relative;padding-top:38px}
.service:last-child{border-right:0}
.service .icon{width:52px;height:52px;margin:0 auto;border:1.5px solid #333;border-radius:50%;display:flex;align-items:center;justify-content:center}
.service h3{font-size:15px;font-weight:500;color:var(--ink);margin-top:24px}
.service p{font-size:11px;line-height:18px;margin-top:12px;color:var(--text)}
.service .more{display:block;margin-top:14px;font-size:12.5px;color:#b5651d}
.service.featured{background:var(--orange);border-color:var(--orange)}
.service.featured h3,.service.featured p{color:var(--white)}
.service.featured .icon{border-color:var(--white)}
.service.featured .more{color:#8a4d12}
.service.featured::after{content:"";position:absolute;left:50%;bottom:-12px;margin-left:-10px;border:10px solid transparent;border-top-color:var(--orange);border-bottom:0;border-top-width:12px}

/* testimonials */
.testimonials{position:absolute;top:1246px;left:0;width:1200px;height:360px;background:linear-gradient(180deg,#2a2226,#1a1518 55%,#3a2a20)}
.testimonials .section-title{position:absolute;top:30px;width:100%;text-align:center;color:var(--white);font-size:26px}
.avatar{position:absolute;left:550px;top:93px;width:105px;height:105px;border-radius:50%;background:linear-gradient(160deg,#6a7f8e,#b9a08a);border:4px solid #111}
.quote{position:absolute;left:250px;width:700px;top:218px;text-align:center;color:#d6d6d6;font-style:italic;font-size:12.5px;line-height:21px}
.author{position:absolute;top:294px;width:100%;text-align:center;color:var(--white);font-size:12.5px}
.author small{color:#bbb;font-size:11px}
.qmark{position:absolute;font-size:80px;color:#aaa;line-height:1;font-weight:700}
.slide-arrow{position:absolute;top:165px}

/* news */
.news-head{top:1650px;height:40px;display:flex;justify-content:space-between;align-items:center}
.news-head .section-title{font-size:27px}
.pager{display:flex;gap:3px}
.pager span{width:26px;height:22px;display:flex;align-items:center;justify-content:center}
.news-list{top:1735px;display:flex;gap:30px}
.news-item{display:flex;gap:14px;width:316px}
.news-thumb{width:158px;height:128px;flex:none}
.news-body h4{font-size:12px;font-weight:500;color:var(--ink);line-height:18px}
.news-meta{font-size:10px;color:var(--muted);margin-top:5px;padding-bottom:5px;border-bottom:1px solid #ddd}
.news-body p{font-size:10px;line-height:15px;margin-top:7px;color:var(--text)}
.news-body .more{display:block;margin-top:10px;font-size:10px;color:var(--accent-red)}

/* footer */
.site-footer{position:absolute;top:1955px;left:0;width:1200px;height:230px;background:var(--footer);color:#ddd}
.footer-col{position:absolute;top:40px}
.footer-col h5{font-size:13px;font-weight:400;color:var(--white)}
.divider{position:absolute;top:40px;width:1px;height:158px;background:#3a3a3a}
.social{display:flex;gap:8px;margin-top:38px}
.social div{width:72px;height:92px;display:flex;flex-direction:column;align-items:center;justify-content:center;gap:12px;color:var(--white);font-size:12px}
.social i{width:32px;height:32px;border-radius:50%;background:rgba(255,255,255,.2)}
.mailing p{font-size:11px;line-height:19px;margin-top:20px;color:#bbb;width:250px}
.signup{display:flex;margin-top:12px}
.signup span{width:200px;height:29px;background:var(--white);color:#aaa;font-size:10px;padding:8px 14px}
.signup b{width:30px;height:29px;background:var(--orange);display:flex;align-items:center;justify-content:center}
.mailing small{display:block;margin-top:8px;font-size:10px;color:#888}
.footer-menu ul{list-style:none;margin-top:24px}
.footer-menu li{font-size:11px;line-height:21.5px;color:#ddd}
.footer-bottom{position:absolute;top:2185px;left:0;width:1200px;height:51px;background:var(--footer-bottom);text-align:center;line-height:51px;font-size:10.5px;color:#777}
</style>
</head>
<body>

<header class="site-header">
  <div class="brand">
    <div class="brand-name">Halvik.</div>
    <div class="brand-tagline">Leadership toolkit for firms on the rise</div>
  </div>
  <nav class="main-nav">
    <a class="active">Home</a><a>About Us</a><a>Services</a><a>Gallery</a><a>Contact Us</a>
  </nav>
</header>

<section class="hero">
  <div class="hero-photo" role="img" aria-label="Photo of a child looking up at a height chart drawn on a white wall"></div>
  <div class="hero-text">We are a consultancy firm focused on<br>growth management for Swedish SME's</div>
  <div class="btn-dark">Read More</div>
  <div class="hero-dots"><span class="on"></span><span></span><span></span></div>
</section>

<section class="wrap about">
  <h2 class="section-title">About Halvik</h2>
  <p>Lorem ipsum dolor sit amet, consectetur adipiscing elit. Fusce tristique ultricies dui et porta. Sed luctus mauris at dictum auctor. Ut sit amet eleifend tortor, vel fermentum ante. Sed luctus tellus eget tortor mollis, in ullamcorper erat facilisis. Pellentesque bibendum nec nisi ut consectetur. Mauris et elit id est luctus dapibus laoreet scelerisque arcu. Nam varius tincidunt enim quis ultricies. Morbi eleifend, dui faucibus gravida pellentesque, dui lectus tristique ante, et tempor metus ante ut mauris. Quisque feugiat massa ut nisi iaculis pulvinar. Ut euismod mauris enim, ac ultrices massa dignissim ac.</p>
  <span class="btn-orange">View More</span>
</section>

<section class="wrap services">
  <div class="service">
    <div class="icon"><svg width="22" height="22" viewBox="0 0 22 22" fill="none" stroke="#333" stroke-width="1.6"><path d="M2 3v17h18"/><path d="M7 16v-5M11 16V8M15 16v-6M18 16v-3"/></svg></div>
    <h3>Growth Management</h3>
    <p>Praesent turpis mauris, aliquet<br>Gravida adipiscing lectus ut rutrum<br>Aenean at posuere risus.</p>
    <span class="more">Read more &nbsp;→</span>
  </div>
  <div class="service">
    <div class="icon"><svg width="22" height="22" viewBox="0 0 22 22" fill="none" stroke="#333" stroke-width="1.6"><path d="M11 2a6 6 0 0 0-3.5 10.9V15h7v-2.1A6 6 0 0 0 11 2z"/><path d="M8.5 17.5h5M9.5 20h3"/></svg></div>
    <h3>Corporate Communication</h3>
    <p>Praesent turpis mauris, aliquet<br>Gravida adipiscing lectus ut rutrum<br>Aenean at posuere risus.</p>
    <span class="more">Read more &nbsp;→</span>
  </div>
  <div class="service featured">
    <div class="icon"><svg width="22" height="22" viewBox="0 0 22 22" fill="none" stroke="#fff" stroke-width="1.6"><rect x="3" y="4" width="16" height="15" rx="1"/><path d="M3 8h16M7 2v4M15 2v4M7 11h2M11 11h2M15 11h1M7 15h2M11 15h2"/></svg></div>
    <h3>Project Management</h3>
    <p>Praesent turpis mauris, aliquet<br>Gravida adipiscing lectus ut rutrum<br>Aenean at posuere risus.</p>
    <span class="more">Read more &nbsp;→</span>
  </div>
  <div class="service">
    <div class="icon"><svg width="22" height="22" viewBox="0 0 22 22" fill="none" stroke="#333" stroke-width="1.6"><path d="M3 10h4v9H3zM7 11l4-8c1.5 0 2 1 2 2l-1 4h6c1 0 2 1 1.7 2.2l-1.5 6c-.3 1-1 1.8-2 1.8H7"/></svg></div>
    <h3>Concepetualizing</h3>
    <p>Praesent turpis mauris, aliquet<br>Gravida adipiscing lectus ut rutrum<br>Aenean at posuere risus.</p>
    <span class="more">Read more &nbsp;→</span>
  </div>
</section>

<section class="testimonials" role="img" aria-label="Night city skyline with a suspension bridge, darkened">
  <h2 class="section-title">Testimonials</h2>
  <div class="avatar" role="img" aria-label="Portrait photo of the client"></div>
  <span class="qmark" style="left:205px;top:165px">“</span>
  <span class="qmark" style="left:960px;top:235px">”</span>
  <p class="quote">Mauris interdum velit leo, ac porta leo vehicula sed. Maecenas iaculis cursus magna. Vestibulum molestie, urna vel lobortis dictum, lacus nibh varius elit, ac tristique sapien dui sit amet diam. Phasellus hendrerit, augue vitae tristique rhoncus, felis urna blandit mauris, vel egestas ex tellus quis leo. Morbi at lacus in.</p>
  <div class="author">Mara Lindholm, <small>Lorme ipsum</small></div>
  <svg class="slide-arrow" style="left:30px" width="24" height="42" viewBox="0 0 24 42" fill="none" stroke="#ddd" stroke-width="1.5"><path d="M22 1L2 21l20 20"/></svg>
  <svg class="slide-arrow" style="right:30px" width="24" height="42" viewBox="0 0 24 42" fill="none" stroke="#ddd" stroke-width="1.5"><path d="M2 1l20 20L2 41"/></svg>
</section>

<section class="wrap news-head">
  <h2 class="section-title">Latest News</h2>
  <div class="pager">
    <span style="background:var(--orange)"><svg width="8" height="10" viewBox="0 0 8 10" fill="none" stroke="#fff" stroke-width="1.6"><path d="M6 1L2 5l4 4"/></svg></span>
    <span style="background:#222"><svg width="8" height="10" viewBox="0 0 8 10" fill="none" stroke="#fff" stroke-width="1.6"><path d="M2 1l4 4-4 4"/></svg></span>
  </div>
</section>

<section class="wrap news-list">
  <article class="news-item">
    <div class="news-thumb" role="img" aria-label="Photo of two colleagues working at a laptop" style="background:linear-gradient(135deg,#c9b8a5,#6f6a6a)"></div>
    <div class="news-body">
      <h4>Lorem ipsum dolor sit amet, consectetur</h4>
      <div class="news-meta">15/05/2016 &nbsp; - &nbsp; Friday</div>
      <p>Mauris interdum velit leo, ac porta leo vehicula sed. Maecenas iaculis</p>
      <span class="more">Read More ⊙</span>
    </div>
  </article>
  <article class="news-item">
    <div class="news-thumb" role="img" aria-label="Photo of a business handshake over documents" style="background:linear-gradient(135deg,#4a5a6c,#9aa6b2)"></div>
    <div class="news-body">
      <h4>Lorem ipsum dolor sit amet, consectetur</h4>
      <div class="news-meta">15/05/2016 &nbsp; - &nbsp; Friday</div>
      <p>Mauris interdum velit leo, ac porta leo vehicula sed. Maecenas iaculis</p>
      <span class="more">Read More ⊙</span>
    </div>
  </article>
  <article class="news-item">
    <div class="news-thumb" role="img" aria-label="Photo of a team meeting by bright office windows" style="background:linear-gradient(135deg,#f2e6cf,#7a6c5c)"></div>
    <div class="news-body">
      <h4>Lorem ipsum dolor sit amet, consectetur</h4>
      <div class="news-meta">15/05/2016 &nbsp; - &nbsp; Friday</div>
      <p>Mauris interdum velit leo, ac porta leo vehicula sed. Maecenas iaculis</p>
      <span class="more">Read More ⊙</span>
    </div>
  </article>
</section>

<footer class="site-footer">
  <div class="footer-col" style="left:98px">
    <h5>Let's Connect</h5>
    <div class="social">
      <div style="background:var(--blue)"><i></i>2598</div>
      <div style="background:var(--sky)"><i></i>4576</div>
      <div style="background:var(--red)"><i></i>1269</div>
    </div>
  </div>
  <div class="divider" style="left:437px"></div>
  <div class="footer-col mailing" style="left:535px">
    <h5>Mailing List</h5>
    <p>Sign up for our mailing list to get latest updates and offers.</p>
    <div class="signup"><span>Email address</span><b><svg width="12" height="10" viewBox="0 0 12 10" fill="none" stroke="#fff" stroke-width="2"><path d="M1 5l3.5 3.5L11 1"/></svg></b></div>
    <small>We respect your privacy</small>
  </div>
  <div class="divider" style="left:875px"></div>
  <div class="footer-col footer-menu" style="left:972px">
    <h5>Menu</h5>
    <ul><li>Home</li><li>About Us</li><li>Services</li><li>Gallery</li><li>Contact Us</li></ul>
  </div>
</footer>
<div class="footer-bottom">© Copyrights 2015 All Rights Reserved</div>

</body>
</html>
```